Accountability Project Graphics

I want to create 10 social media graphics (new Instagram size 4:5 (1080 x 1350 pixels) focusing on our Quilvo Accountability App, using any of the 3 pictures attached. Use the attached pics only, NO RANDOM STOCK PHOTOGRAPHY. For the color scheme, use the landing page colors/fonts (attached).
You can add any of the 3 photos attached but I mainly need BOLD text that includes these headlines and sub-headlines on them.
Please NOTE for all the headlines below, also add this sub-headline on each graphic:
Stay Consistent with RT in Your Pocket!
Here are the headlines:
• Stop Starting Over Every Monday
• You don't need more willpower. You need more support
• Built for women who are tired of doing this alone
• When Motivation Fades, RT Checks In
• The Support System You've Been Missing
• Support When Motivation Disappears
• What if RT Checked in Every Day?
• The Missing Piece Isn't Another Diet
• Eat the food you love. Stay accountable every day.
• One Bad Meal Doesn't Mean You Failed
women over 40 trying to lose weight

```html
<!DOCTYPE html>
<html lang="en">
<head>
<meta charset="utf-8">
<title>Quilvo Accountability App – Social Graphics</title>
<link rel="stylesheet" href="https://fonts.googleapis.com/css2?family=Playfair+Display:ital,wght@0,700;0,800;0,900;1,700;1,800;1,900&display=swap">
<style>
  :root {
    --board: #555555;
    --blush: #fde3e9;
    --blush-light: #fff0f4;
    --plum: #2e1a40;
    --rose: #d14f7f;
    --photo-warm: #b98a78;
    --photo-dark: #262a44;
    --photo-denim: #3d4f72;
  }
  * { margin: 0; padding: 0; box-sizing: border-box; }
  html, body { width: 1200px; height: 751px; overflow: hidden; background: var(--board); }
  body { position: relative; font-family: "Playfair Display", Georgia, serif; }

  .post { position: absolute; overflow: hidden; background: linear-gradient(160deg, var(--blush-light), var(--blush)); }
  .post--feature { left: 45px; top: 38px; width: 540px; height: 676px; }
  .post--tile { width: 170px; height: 213px; }
  .col-1 { left: 609px; } .col-2 { left: 798px; } .col-3 { left: 995px; }
  .row-1 { top: 38px; } .row-2 { top: 270px; } .row-3 { top: 498px; }

  .line { position: absolute; z-index: 2; line-height: 1; white-space: nowrap; font-weight: 800; }
  .plum { color: var(--plum); }
  .rose { color: var(--rose); }
  .italic { font-style: italic; }
  .black { font-weight: 900; }
  .subline { position: absolute; z-index: 2; color: var(--plum); font-style: italic; font-weight: 700; font-size: 7px; line-height: 1.2; }
  .subline--feature { font-size: 20px; font-weight: 800; line-height: 1.25; }

  .photo { position: absolute; z-index: 1; }
  .photo--solo { background: linear-gradient(180deg, rgba(185,138,120,0) 0%, var(--photo-warm) 18%, var(--photo-dark) 40%, var(--photo-dark) 85%, rgba(38,42,68,0) 100%); border-radius: 40% 40% 6px 6px; }
  .photo--duo { background: linear-gradient(100deg, rgba(61,79,114,0) 0%, var(--photo-denim) 20%, #e9e4e6 55%, var(--photo-denim) 85%, rgba(61,79,114,0) 100%); border-radius: 30% 30% 4px 4px; opacity: .85; }
  .photo--hug { background: linear-gradient(120deg, #c6a6d6 0%, #4a3a78 35%, #c98a88 60%, #e0508c 85%, rgba(253,227,233,0) 100%); opacity: .8; }
  .fade-bottom { -webkit-mask-image: linear-gradient(180deg, #000 70%, transparent); mask-image: linear-gradient(180deg, #000 70%, transparent); }
  .fade-left { -webkit-mask-image: linear-gradient(90deg, transparent, #000 35%); mask-image: linear-gradient(90deg, transparent, #000 35%); }

  .halo { position: absolute; left: 238px; top: 352px; width: 390px; height: 390px; border-radius: 50%; background: var(--blush-light); }
  .vertical-word { position: absolute; z-index: 2; left: 4px; top: 210px; transform: rotate(-90deg); transform-origin: 0 0; font-size: 50px; font-weight: 900; color: var(--plum); line-height: 1; }
</style>
</head>
<body>

<!-- Feature post -->
<section class="post post--feature">
  <div class="halo"></div>
  <div class="photo photo--solo" style="left:293px; top:235px; width:247px; height:441px;" role="img" aria-label="Portrait of the coach smiling, hand on hip, in a black lace top"></div>
  <div class="line plum black" style="left:34px; top:18px; font-size:118px;">Stop</div>
  <div class="line plum black italic" style="left:28px; top:122px; font-size:118px;">Starting</div>
  <div class="line plum" style="left:30px; top:238px; font-size:66px;">Over</div>
  <div class="line rose" style="left:30px; top:300px; font-size:66px;">Every</div>
  <div class="line rose" style="left:30px; top:360px; font-size:66px;">Monday</div>
  <p class="subline subline--feature" style="left:32px; top:452px; width:250px;">Stay Consistent with RT<br>in Your Pocket!</p>
</section>

<!-- Built for women -->
<section class="post post--tile col-1 row-1">
  <div class="photo photo--duo fade-bottom" style="left:60px; top:71px; width:110px; height:142px;" role="img" aria-label="Two women laughing together, one in denim, one in white"></div>
  <div class="line rose" style="left:0; width:170px; text-align:center; top:8px; font-size:19px;">Built for</div>
  <div class="line rose italic black" style="left:0; width:170px; text-align:center; top:22px; font-size:40px;">women</div>
  <div class="line plum" style="left:9px; top:70px; font-size:14px; line-height:1.3;">who are<br>tired of<br>doing<br>this<br>alone</div>
  <p class="subline" style="left:9px; top:168px; width:52px;">Stay Consistent with RT in Your Pocket!</p>
</section>

<!-- One bad meal -->
<section class="post post--tile col-2 row-1">
  <div class="photo photo--solo fade-left" style="left:86px; top:0; width:84px; height:213px;" role="img" aria-label="The coach standing and smiling in a black lace outfit"></div>
  <div class="line plum" style="left:12px; top:22px; font-size:16px;">One</div>
  <div class="line plum" style="left:12px; top:42px; font-size:16px;">Bad Meal</div>
  <div class="line rose italic" style="left:10px; top:62px; font-size:25px;">Doesn't</div>
  <div class="line rose italic" style="left:10px; top:88px; font-size:25px;">Mean</div>
  <div class="line plum italic" style="left:10px; top:116px; font-size:31px;">You</div>
  <div class="line plum italic" style="left:8px; top:147px; font-size:31px;">Failed</div>
  <p class="subline" style="left:10px; top:188px; width:84px;">Stay Consistent with RT in Your Pocket!</p>
</section>

<!-- Eat the food you love -->
<section class="post post--tile col-3 row-1">
  <div class="photo photo--duo fade-bottom" style="left:0; top:95px; width:110px; height:118px;" role="img" aria-label="Two women embracing and laughing"></div>
  <div class="line plum italic" style="left:70px; top:8px; font-size:15px;">Eat the</div>
  <div class="line plum italic black" style="left:8px; top:18px; font-size:54px;">food</div>
  <div class="line rose italic" style="left:40px; top:70px; font-size:29px;">you love</div>
  <div class="line plum italic" style="right:12px; top:102px; font-size:8.5px; text-align:right; line-height:1.1;">Stay<br>accountable</div>
  <div class="line rose italic" style="right:12px; top:123px; font-size:19px; text-align:right; line-height:1;">every<br>day.</div>
  <p class="subline" style="right:10px; top:166px; width:54px; text-align:right;">Stay Consistent with RT in Your Pocket!</p>
</section>

<!-- Missing piece -->
<section class="post post--tile col-1 row-2">
  <div class="photo photo--hug fade-left" style="left:0; top:112px; width:170px; height:101px;" role="img" aria-label="Two women hugging joyfully in a store"></div>
  <div class="line plum italic" style="left:15px; top:10px; font-size:14px;">The</div>
  <div class="line rose italic" style="left:9px; top:20px; font-size:37px;">Missing</div>
  <div class="line plum italic black" style="left:8px; top:57px; font-size:40px;">Piece</div>
  <div class="line plum italic" style="left:124px; top:67px; font-size:8px; line-height:1.1;">isn't<br>another<br>diet</div>
  <p class="subline" style="left:0; width:170px; top:101px; text-align:center;">Stay Consistent with RT in Your Pocket!</p>
</section>

<!-- What if RT checked in -->
<section class="post post--tile col-2 row-2">
  <div class="photo photo--solo" style="left:50px; top:64px; width:116px; height:149px;" role="img" aria-label="The coach smiling with hand on hip"></div>
  <div class="line plum italic" style="left:0; width:170px; text-align:center; top:11px; font-size:14.5px;">What if RT Checked in</div>
  <div class="line rose" style="left:0; width:170px; text-align:center; top:28px; font-size:44px; letter-spacing:-1px;">EVERY</div>
  <div class="line plum" style="right:10px; top:70px; font-size:22px;">Day?</div>
  <p class="subline" style="left:8px; top:150px; width:42px;">Stay Consistent with RT in Your Pocket!</p>
</section>

<!-- Support system -->
<section class="post post--tile col-3 row-2">
  <div class="photo photo--hug fade-left" style="left:60px; top:0; width:110px; height:213px; opacity:.45;" role="img" aria-label="Two women hugging and laughing, faded behind text"></div>
  <div class="line plum italic" style="left:11px; top:14px; font-size:23px;">The</div>
  <div class="line plum italic" style="left:11px; top:39px; font-size:23px;">Support</div>
  <div class="line plum italic" style="left:11px; top:64px; font-size:23px;">System</div>
  <div class="line rose" style="left:11px; top:96px; font-size:30px;">You've</div>
  <div class="line rose" style="left:11px; top:127px; font-size:30px;">Been</div>
  <div class="line rose" style="left:11px; top:158px; font-size:30px;">Missing</div>
  <p class="subline" style="left:11px; top:198px; width:155px; white-space:nowrap;">Stay Consistent with RT in Your Pocket!</p>
</section>

<!-- When motivation fades -->
<section class="post post--tile col-1 row-3">
  <div class="photo photo--solo fade-left" style="left:77px; top:0; width:93px; height:110px;" role="img" aria-label="The coach smiling in a black lace top"></div>
  <div class="line plum italic" style="left:15px; top:84px; font-size:28px;">When</div>
  <div class="line plum italic" style="left:12px; top:109px; font-size:27px;">Motivation</div>
  <div class="line rose" style="left:0; width:170px; text-align:center; top:136px; font-size:40px;">FADES</div>
  <p class="subline" style="left:0; width:170px; top:182px; text-align:center;">Stay Consistent with RT in Your Pocket!</p>
  <div class="line plum italic" style="left:0; width:170px; text-align:center; top:196px; font-size:10px;">RT Checks In</div>
</section>

<!-- Support when motivation disappears -->
<section class="post post--tile col-2 row-3">
  <div class="photo photo--duo" style="left:50px; top:104px; width:120px; height:109px;" role="img" aria-label="Two women standing together laughing"></div>
  <div class="vertical-word">Support</div>
  <div class="line plum italic" style="left:60px; top:11px; font-size:20px;">When</div>
  <div class="line rose italic" style="left:59px; top:34px; font-size:18px;">Motivation</div>
  <div class="line rose italic" style="left:59px; top:58px; font-size:18px;">Disappears</div>
  <p class="subline" style="left:60px; top:82px; width:105px;">Stay Consistent with RT in Your Pocket!</p>
</section>

<!-- More support -->
<section class="post post--tile col-3 row-3">
  <div class="photo photo--hug fade-bottom" style="left:0; top:0; width:170px; height:104px;" role="img" aria-label="Two women hugging joyfully in a store"></div>
  <div class="line plum" style="left:0; width:170px; text-align:center; top:104px; font-size:12.5px; line-height:1.12;">You don't need<br>more willpower.</div>
  <div class="line rose" style="left:0; width:170px; text-align:center; top:133px; font-size:10px;">You need</div>
  <div class="line rose italic black" style="left:0; width:170px; text-align:center; top:141px; font-size:35px;">more</div>
  <div class="line rose italic" style="left:0; width:170px; text-align:center; top:168px; font-size:26px;">support</div>
  <p class="subline" style="left:0; width:170px; top:200px; text-align:center;">Stay Consistent with RT in Your Pocket!</p>
</section>

</body>
</html>
```